Buch-/eBook-Cover für Krimi
Er hat genau die Vorgaben umgesetzt und sich mit mir sehr kooperativ ausgetauscht
Zielgruppe
Krimileser
Aufgabenstellung
Auf dem Cover muss stehen:
Harald Bruck
Die Spur der gläsernen Reiter
Ein Fall für den bayerischen Barnaby Quince
Wie der Untertitel sagt, habe ich eine Reihe um den Franz Kiefer gestartet, der eine Art bayerischer Barnaby Quince ist. Er hat eine kalte Meerschaumpfeife im Mund, weil er sich das Rauchen abgewöhnt, und trägt bayerische Tracht inkl. Hut. Sein Sidekick ist allerdings Frau Dr. Brunner. Die Pilbury-Figur, aus deren Sicht die Geschichte erzählt wird, ist also eine Frau. Die weißen Soldaten sind Auomaten aus dem 19. Jahrhundert, die Marschmusik spielen und der Schlüssel zu einem spektakulären Schatz sind. Dass es sich um Automaten handelt, sollte natürlich nicht im Cover vorweggenommen werden. Stilisierte weiße Soldaten aus dem 18. oder 19. Jahrhundert kann man aber durchaus einbringen. Prinzipiell hätte ich gerne eine Reminiszenz an den klassischen Barnaby Quince in bayerischem Gewand und zeitgenössisch. Der Roman spielt im Jahr 2023

```html
<!DOCTYPE html>
<html lang="de">
<head>
<meta charset="utf-8">
<title>Harald Bruck – Die Spur der gläsernen Reiter</title>
<link rel="stylesheet" href="https://fonts.googleapis.com/css2?family=Josefin+Sans:wght@300&family=Alegreya:wght@400&display=swap">
<style>
  :root {
    --paper: #f7f7f7;
    --ink: #111111;
    --mist-light: #efefef;
    --mist-mid: rgba(150,150,150,0.55);
    --mist-dark: rgba(110,110,110,0.7);
    --mist-clear: rgba(247,247,247,0);
  }
  html, body {
    margin: 0;
    padding: 0;
    overflow: hidden;
    background: var(--paper);
  }
  .cover {
    position: relative;
    width: 800px;
    height: 1200px;
    overflow: hidden;
    background: var(--paper);
  }
  .cover-artwork {
    position: absolute;
    left: 0;
    top: 250px;
    width: 800px;
    height: 900px;
    background:
      radial-gradient(ellipse 14% 42% at 78% 52%, var(--mist-dark) 0%, var(--mist-mid) 40%, var(--mist-clear) 100%),
      radial-gradient(ellipse 12% 40% at 56% 44%, var(--mist-mid) 0%, rgba(170,170,170,0.35) 45%, var(--mist-clear) 100%),
      radial-gradient(ellipse 11% 38% at 35% 46%, var(--mist-mid) 0%, rgba(170,170,170,0.3) 45%, var(--mist-clear) 100%),
      radial-gradient(ellipse 10% 34% at 17% 44%, rgba(150,150,150,0.4) 0%, rgba(180,180,180,0.25) 45%, var(--mist-clear) 100%),
      linear-gradient(180deg, var(--paper) 0%, var(--mist-light) 20%, var(--mist-light) 80%, var(--paper) 100%);
  }
  .author {
    position: absolute;
    top: 135px;
    left: 0;
    width: 800px;
    margin: 0;
    text-align: center;
    font-family: "Josefin Sans", sans-serif;
    font-weight: 300;
    font-size: 60px;
    font-variant: small-caps;
    letter-spacing: 5px;
    color: var(--ink);
  }
  .title-block {
    position: absolute;
    top: 892px;
    left: 0;
    width: 800px;
    text-align: center;
    color: var(--ink);
  }
  .title {
    margin: 0;
    font-family: "Alegreya", serif;
    font-weight: 400;
    font-size: 50px;
    line-height: 55px;
  }
  .subtitle {
    margin: 34px 0 0;
    font-family: "Alegreya", serif;
    font-weight: 400;
    font-size: 24px;
    letter-spacing: 0.3px;
  }
</style>
</head>
<body>
  <main class="cover">
    <div class="cover-artwork" role="img" aria-label="Vier schemenhafte Soldaten mit Hüten und Gewehren, die im weißen Nebel nach rechts marschieren"></div>
    <h2 class="author">Harald Bruck</h2>
    <div class="title-block">
      <h1 class="title">Die Spur der<br>gläsernen Reiter</h1>
      <p class="subtitle">Ein Fall für den bayerischen Barnaby Quince</p>
    </div>
  </main>
</body>
</html>
```